Harrow Grading LLC business card design

Excavation company business cards

Contact Information for Business Card

Harrow Grading LLC cell phone 208-417-6290 office phone 208-319-4856 harrowgradingllc@maplecove.com Driveways, site prep, retaining walls, septic systems, rock delivery

Colors

Designer to choose colors to be used in the design.

```html
<!DOCTYPE html>
<html lang="en">
<head>
<meta charset="utf-8">
<title>Harrow Grading LLC – Business Card</title>
<link href="https://fonts.googleapis.com/css2?family=Roboto:wght@400;500;700;900&display=swap" rel="stylesheet">
<style>
  :root {
    --orange: #ec6f24;
    --orange-deep: #d85f19;
    --orange-soft: #f07d38;
    --white: #ffffff;
    --ink: #2b2b2b;
    --grey: #5c5c5c;
    --backdrop: #c6c6c6;
  }
  * { box-sizing: border-box; margin: 0; padding: 0; }
  html, body { width: 1200px; height: 788px; overflow: hidden; }
  body {
    background: linear-gradient(180deg, #d2d2d2 0%, #b4b4b4 100%);
    font-family: "Roboto", sans-serif;
    position: relative;
  }

  /* ---------- Front card ---------- */
  .card-front {
    position: absolute;
    left: 150px; top: 104px;
    width: 340px; height: 580px;
    border-radius: 22px;
    background: var(--white);
    overflow: hidden;
    box-shadow: 0 10px 26px rgba(0,0,0,.28);
  }
  .brand-mark {
    position: absolute; top: 78px; left: 0; right: 0;
    display: flex; flex-direction: column; align-items: center; gap: 10px;
  }
  .brand-dot {
    width: 46px; height: 46px; border-radius: 50%;
    background: var(--orange);
  }
  .brand-name {
    font-weight: 900; font-size: 30px; letter-spacing: 1px;
    color: var(--orange); text-transform: uppercase; text-align: center; line-height: 1.05;
  }
  .holder {
    position: absolute; top: 236px; left: 0; right: 0; text-align: center;
  }
  .holder-name {
    font-weight: 700; font-size: 22px; color: var(--orange); letter-spacing: .5px;
  }
  .holder-role {
    font-style: italic; font-size: 15px; color: var(--ink); margin-top: 4px;
  }
  .contact-band {
    position: absolute; left: 0; right: 0; bottom: 0; height: 300px;
    background: var(--orange);
    clip-path: polygon(0 0, 100% 14%, 100% 100%, 0 100%);
  }
  .divider {
    position: absolute; left: 0; top: 280px; width: 340px; height: 48px;
  }
  .contact-icons {
    position: absolute; top: 300px; left: 92px;
    display: flex; gap: 8px;
  }
  .contact-icon {
    width: 28px; height: 28px; border-radius: 50%;
    background: var(--grey); border: 2px solid var(--white);
    display: flex; align-items: center; justify-content: center;
  }
  .contact-list {
    position: absolute; top: 360px; left: 0; right: 0;
    text-align: center; color: var(--white); font-size: 15px; line-height: 1.55;
  }
  .contact-rule {
    width: 250px; height: 1px; background: var(--white); margin: 12px auto;
  }

  /* ---------- Back card ---------- */
  .card-back {
    position: absolute;
    left: 560px; top: 229px;
    width: 500px; height: 330px;
    border-radius: 22px;
    background: var(--orange);
    overflow: hidden;
    box-shadow: 0 10px 26px rgba(0,0,0,.28);
  }
  .back-pattern {
    position: absolute; inset: 0;
    background: linear-gradient(135deg, var(--orange-soft) 0%, var(--orange) 50%, var(--orange-deep) 100%);
  }
  .back-brand {
    position: absolute; left: 170px; top: 120px;
    display: flex; align-items: center; gap: 10px;
  }
  .back-dot { width: 28px; height: 28px; border-radius: 50%; background: var(--white); }
  .back-name {
    font-weight: 900; font-size: 24px; color: var(--white); text-transform: uppercase; letter-spacing: 1px;
  }
  .services {
    position: absolute; left: 28px; top: 30px; bottom: 30px;
    display: flex; flex-direction: column; justify-content: center; gap: 8px;
    color: var(--white); font-size: 15px;
  }
</style>
</head>
<body>

<section class="card-front" aria-label="Business card front">
  <div class="brand-mark">
    <div class="brand-dot"></div>
    <div class="brand-name">Harrow Grading LLC</div>
  </div>

  <div class="holder">
    <div class="holder-name">DANA WHITLOCK</div>
    <div class="holder-role">Founder</div>
  </div>

  <div class="contact-band"></div>
  <svg class="divider" viewBox="0 0 340 48" aria-hidden="true">
    <line x1="0" y1="0" x2="340" y2="42" stroke="#5c5c5c" stroke-width="2"/>
  </svg>

  <div class="contact-icons">
    <span class="contact-icon">
      <svg width="14" height="14" viewBox="0 0 24 24"><path fill="#fff" d="M6.6 10.8a15 15 0 0 0 6.6 6.6l2.2-2.2c.3-.3.7-.4 1-.2 1.1.4 2.3.6 3.6.6.6 0 1 .4 1 1V20c0 .6-.4 1-1 1A17 17 0 0 1 3 4c0-.6.4-1 1-1h3.5c.6 0 1 .4 1 1 0 1.3.2 2.5.6 3.6.1.3 0 .7-.2 1z"/></svg>
    </span>
    <span class="contact-icon">
      <svg width="14" height="14" viewBox="0 0 24 24"><rect x="6" y="2" width="12" height="20" rx="2" fill="none" stroke="#fff" stroke-width="2"/><circle cx="12" cy="18" r="1.2" fill="#fff"/></svg>
    </span>
    <span class="contact-icon">
      <svg width="14" height="14" viewBox="0 0 24 24"><rect x="3" y="5" width="18" height="14" rx="1" fill="none" stroke="#fff" stroke-width="2"/><path d="M3 6l9 7 9-7" fill="none" stroke="#fff" stroke-width="2"/></svg>
    </span>
    <span class="contact-icon">
      <svg width="14" height="14" viewBox="0 0 24 24"><circle cx="12" cy="12" r="9" fill="none" stroke="#fff" stroke-width="2"/><ellipse cx="12" cy="12" rx="4" ry="9" fill="none" stroke="#fff" stroke-width="1.5"/><line x1="3" y1="12" x2="21" y2="12" stroke="#fff" stroke-width="1.5"/></svg>
    </span>
  </div>

  <div class="contact-list">
    <div>208-319-4856</div>
    <div>208-417-6290</div>
    <div>harrowgradingllc@maplecove.com</div>
    <div>www.harrowgradingllc.com</div>
    <div class="contact-rule"></div>
    <div>4587 Street Address Name</div>
    <div>Country Name AB 4581</div>
  </div>
</section>

<section class="card-back" aria-label="Business card back">
  <div class="back-pattern" role="img" aria-label="Repeating tone-on-tone pattern of small excavator and mountain motifs"></div>
  <ul class="services" style="list-style:none">
    <li>Driveways</li>
    <li>Site Prep</li>
    <li>Retaining Walls</li>
    <li>Rock Delivery</li>
    <li>Septic Systems</li>
  </ul>
  <div class="back-brand">
    <span class="back-dot"></span>
    <span class="back-name">Harrow Grading LLC</span>
  </div>
</section>

</body>
</html>
```